Flyer for an pediatric sleep consultancy - to distribute to play and childcare centers etc.

I need a flyer that will attract the attention of parents with children between the age of babies to toddlers, who may be experiencing sleep issues. The flyer will be placed at places such as community centers, doctors room, play centers, kindergardens, etc.

My company is called "The Quiet Meadow Nest" and provides a sleep consultancy service. My service essentially provides a customized plan for parents to follow and general advice and guidance. It is not medical advice.

I like to the flyer to have an overall tone that is soft and peaceful with a clean and beautiful design, however can catch the attention of parents who may be struggling with their child's sleep issues and are sleep deprived. I would like photos with minimal text. The colour I use is a brownish rose. I will attach some of my designs to give you an idea. You can have a look at my homepage as well to get an idea about my esthetic direction and the colour. Although the colour of my page is a bit too brownish....

I will provide the text to appear in the flyer once I have a better idea of the layout that I prefer for the flyer. The text however wont be extensive, just some catchy points.

I want to direct people to my website which is www.quietmeadownest-example.com
I offer a first FREE evaluation call, to the parents, to get to know each other better, learn about their child's particular sleep problems and see if we are a good fit and can work together. I would like to have this information somehow on the flyer, so that the parents will contact me.
I also have a facebook page, which is: The Quiet Meadow Nest

I have a logo that I would like to appear on the flyer. I will attach the file once the uploader on pixel guild is fixed.

When I print the flyer - I like to print A5 SIZE ... please make sure the formatting is OK for this size.

Here are some text ideas. of course all of it would be too much, I guess. On the front of the flyer I would like to have some catchy phrase or something similar to get people interested and to want to know more. On the back there could be a bit more text and information. But I'm open too suggestions....
I'm not too sure about the wording yet. But here are some text that I might be use:

Is sleep an issue in your home?

Is your baby having trouble sleeping? ... are you?!
I can help!

Sleep, baby, sleep….

Teaching children how to sleep

The Quiet Meadow Nest is a pediatric sleep consultancy that specializes in helping parents with children who struggle to develop good and healthy sleep habits.
Disruptive sleep patterns or not enough sleep can affect the physical, mental and emotional development of your child.

Of course nobody plans to have a sleep problem, but habits can become easily ingrained and spiral quickly out of control and you can find yourself sleep deprived, desperate and not too sure what to do. You see all the other sleeping babies and wish there was someone who understood what you were going through?! Well, there is!

Contact me for a free 15 minute consultation.

This 15 minute „mini“ consultation is a chance to discuss your unique sleep challenges and sleep goals with me. I will provide you with an overview of how I will work with your family to achieve your wildest sleep dreams (goals).
Furthermore do I understand and believe that every child and their family is unique and there is no one size fits all!
I would love to have a chat with you and talk about how I can help make things easier for you and your family!

Do I need a sleep consultant for my child?
The answer is yes if:
- if your child will only fall asleep when nursing or bottle feeding
- if your child needs a dummy or other external aid, like being rocked, patted or taken for a care ride to fall asleep
- if your good night routine is a challenging and exhausting procedure instead of a relaxed and enjoyable moment for the whole family
- if sleep is a constant battle in your home which leaves you feeling frustrated and exhausted
- if your own lack of sleep is taking a toll on you and the whole family

What can I do for you?

I will:

- Guide you to set an age appropriate foundation for good sleep
- Create an individual sleep plan tailored especially to your child’s sleep needs and circumstances
- Help you to teach your childto go to sleep and get back to sleep independently during the night
- show you how to teach your child to take healthful, restorative naps
-Learn

Contact:

Marta Lindqvist
info@quietmeadownest-example.com
www.quietmeadownest-example.com
+34 612 384 705

Consultations in English, German or Spanish via Phone/Skype or home consultation
Updates

Project Deadline Extended
Reason: I have to go on a business trip and won't be able to choose a design until the deadline. During the trip I won't have time to give feedback and ask for changes. thank you

Target Market(s)

parents, sleep deprived mothers, young families, child care provider,

Industry/Entity Type

Baby Care

Contact Information for Business Card

Marta Lindqvist
pediatric sleep consultant
+34 612 384 705

```html
<!DOCTYPE html>
<html lang="en">
<head>
<meta charset="utf-8">
<title>The Quiet Meadow Nest – Flyer</title>
<link rel="stylesheet" href="https://fonts.googleapis.com/css2?family=Lustria&family=Lato:ital,wght@0,300;0,400;1,400&family=Yanone+Kaffeesatz:wght@300;500&display=swap">
<style>
:root{
  --rose:#c98676;
  --rose-deep:#c4705f;
  --rose-soft:#dbb0a5;
  --sage:#5d7b70;
  --sage-grey:#8fa29a;
  --ink:#222;
  --panel:#eef0ef;
  --page:#ffffff;
  --stage:#f1eeec;
}
*{box-sizing:border-box;margin:0;padding:0}
html,body{width:1200px;height:1200px;overflow:hidden;background:var(--stage)}
body{position:relative;font-family:'Lato',sans-serif;color:var(--ink)}
.page{position:absolute;top:222px;width:540px;height:756px;background:var(--page);overflow:hidden}
.front{left:40px}
.back{left:620px}
.abs{position:absolute}
.photo{background:radial-gradient(ellipse at 60% 40%,#f6dccf 0%,#efe4df 45%,#e7e7e8 100%)}
.photo-round{border-radius:50%;border:6px solid var(--sage-grey);background:radial-gradient(circle at 55% 45%,#f3d8cc,#e9e4e2 70%)}
.photo-round.white{border-color:#fff;box-shadow:0 0 0 1px #ddd}
.headline{font-family:'Lustria',serif;font-size:38px;line-height:43px;left:40px;top:26px}
.headline .l1{color:var(--rose)}
.headline .l2{color:var(--sage)}
.brand{font-family:'Lato',sans-serif;font-weight:300;color:var(--sage-grey);display:flex;align-items:center;gap:8px;white-space:nowrap}
.brand .dot{width:14px;height:14px;border-radius:50%;background:var(--rose-soft)}
.free-badge{left:305px;top:272px;width:212px;height:212px;border-radius:50%;background:var(--rose-deep);border:7px solid #fff;box-shadow:0 2px 6px rgba(0,0,0,.15);text-align:center;color:#fff;font-family:'Yanone Kaffeesatz',sans-serif}
.free-badge .big{font-size:62px;font-weight:500;line-height:1;margin-top:26px;letter-spacing:1px}
.free-badge .small{font-size:32px;font-weight:300;line-height:1}
.eyebrow{left:46px;top:428px;font-family:'Lustria',serif;font-size:14px;color:var(--sage);letter-spacing:.5px}
.title{left:46px;top:446px;font-family:'Lustria',serif;font-size:27px;color:var(--rose-deep);letter-spacing:.5px}
.intro{left:46px;top:490px;width:460px;font-size:12.4px;line-height:15px}
.intro p+p{margin-top:14px}
.contact-h{font-family:'Lato',sans-serif;font-weight:300;color:var(--rose-deep)}
.contact-name{font-family:'Lato',sans-serif;font-weight:300;color:var(--sage)}
.contact-list{list-style:none;font-size:14.5px}
.contact-list li{display:flex;align-items:center;gap:8px;height:22px}
.ico{width:10px;height:10px;flex:none}
.cta{left:40px;top:122px;width:468px;height:34px;border-radius:17px;background:var(--rose);border:2px solid #c47868;color:#fff;font-family:'Lustria',serif;font-size:19.5px;text-align:center;line-height:30px}
.blurb{left:33px;top:166px;width:488px;font-size:8.9px;line-height:12.5px;color:#111}
.panel{left:0;top:232px;width:540px;height:420px;background:linear-gradient(#eef0ef,#f6f6f6)}
.col-h{font-size:12px;color:var(--sage);line-height:15px;font-weight:400}
.col-sub{font-size:11px;font-style:italic;color:var(--sage);margin-top:6px}
.bullets{list-style:none;margin-top:6px;font-size:8.3px;font-style:italic;line-height:11.8px;color:#222}
.bullets li{position:relative;padding-left:0;text-align:justify}
.bullets li::before{content:"";position:absolute;left:-8px;top:4px;width:3px;height:3px;border-radius:50%;background:var(--rose)}
.bullets.wide li{line-height:16px;margin-bottom:0}
.divider{background:var(--sage-grey);width:1px}
</style>
</head>
<body>

<!-- FRONT -->
<section class="page front">
  <div class="abs photo" style="left:0;top:0;width:540px;height:320px" role="img" aria-label="Close-up photograph of a sleeping baby holding its hands together on soft white bedding"></div>
  <h1 class="abs headline"><span class="l1">Sleep, Baby,</span><br><span class="l2">Sleep...</span></h1>

  <svg class="abs" style="left:0;top:240px" width="540" height="180" viewBox="0 0 540 180">
    <path d="M0 30 C120 0 260 0 340 40 C420 80 480 70 540 58 L540 180 L0 180Z" fill="var(--sage-grey)"/>
    <path d="M0 40 C120 12 260 14 340 52 C420 88 480 82 540 72 L540 180 L0 180Z" fill="#fff"/>
    <path d="M0 128 C120 160 260 150 360 120 C440 98 500 100 540 108 L540 118 C500 112 440 112 360 134 C260 162 120 172 0 148Z" fill="var(--rose-soft)"/>
  </svg>
  <div class="abs brand" style="left:26px;top:320px;font-size:18px"><span class="dot"></span>The Quiet Meadow Nest</div>

  <div class="abs free-badge"><div class="big">FREE</div><div class="small">Evaluation Call</div></div>

  <div class="abs eyebrow">TEACHING CHILDREN</div>
  <h2 class="abs title">HOW TO SLEEP</h2>
  <div class="abs intro">
    <p>The Quiet Meadow Nest is a pediatric sleep consultancy that specializes in helping parents with children who struggle to develop good and healthy sleep habits.</p>
    <p>Disruptive sleep patterns or not enough sleep can affect the physical, mental and emotional development of your child.</p>
  </div>

  <svg class="abs" style="left:0;top:580px" width="540" height="60" viewBox="0 0 540 60">
    <path d="M0 40 C140 0 300 0 420 40 C470 56 510 50 540 38" fill="none" stroke="var(--rose-soft)" stroke-width="5"/>
  </svg>

  <div class="abs contact-h" style="left:46px;top:612px;font-size:21px">Contact Us:</div>
  <div class="abs contact-name" style="left:46px;top:642px;font-size:19px">Marta Lindqvist</div>
  <ul class="abs contact-list" style="left:28px;top:668px">
    <li><svg class="ico" viewBox="0 0 10 10"><rect x="1" y="2" width="8" height="6" fill="none" stroke="var(--rose)" stroke-width="1.3"/><path d="M1 2 L5 5.5 L9 2" fill="none" stroke="var(--rose)" stroke-width="1.1"/></svg>info@quietmeadownest-example.com</li>
    <li><svg class="ico" viewBox="0 0 10 10"><circle cx="5" cy="5" r="3.8" fill="none" stroke="var(--rose)" stroke-width="1.3"/><path d="M1.2 5 H8.8" stroke="var(--rose)" stroke-width="1"/></svg>www.quietmeadownest-example.com</li>
    <li><svg class="ico" viewBox="0 0 10 10"><path d="M2 1 L4 1 L4.6 3.3 L3.4 4.2 C4 5.6 4.6 6.2 5.8 6.8 L6.8 5.6 L9 6.2 L9 8.2 C6 9.5 0.6 4 2 1Z" fill="var(--rose)"/></svg>+34 612 384 705</li>
  </ul>

  <div class="abs photo-round white" style="left:342px;top:576px;width:158px;height:158px" role="img" aria-label="Photograph of a mother resting her cheek beside her sleeping newborn"></div>
</section>

<!-- BACK -->
<section class="page back">
  <div class="abs brand" style="left:0;width:540px;justify-content:center;top:68px;font-size:18px"><span class="dot"></span>The Quiet Meadow Nest</div>
  <div class="abs cta">Contact me for a free 15 minute consultation</div>
  <p class="abs blurb">This 15 minute „mini“ consultation is a chance to discuss your unique sleep challenges and sleep goals with me. I will provide you with an overview of how I will work with your family to achieve your wildest sleep dreams (goals). Furthermore do I understand and believe that every child and their family is unique and there is no one size fits all! I would love to have a chat with you and talk about how I can help make things easier for you and your family!</p>

  <div class="abs panel"></div>
  <div class="abs divider" style="left:270px;top:252px;height:196px"></div>

  <div class="abs" style="left:39px;top:250px;width:202px">
    <h3 class="col-h">Do I need a sleep consultant<br>for my child?</h3>
    <div class="col-sub">The answer is yes if:</div>
    <ul class="bullets">
      <li>If your child will only fall asleep when nursing or bottle feeding</li>
      <li>If your child needs a dummy or other external aid, like being rocked, patted or taken for a care ride to fall asleep</li>
      <li>If your good night routine is a challenging and exhausting procedure instead of a relaxed and enjoyable moment for the whole family</li>
      <li>If sleep is a constant battle in your home which leaves you feeling frustrated and exhausted</li>
      <li>If your own lack of sleep is taking a toll on you and the whole family</li>
    </ul>
  </div>

  <div class="abs" style="left:300px;top:250px;width:210px">
    <h3 class="col-h">What can I do for you?</h3>
    <div class="col-sub" style="margin-top:10px">I will</div>
    <ul class="bullets wide">
      <li>Guide you to set an age appropriate foundation for good sleep</li>
      <li>Create an individual sleep plan tailored especially to your child's sleep needs and circumstances</li>
      <li>Help you to teach your childto go to sleep and get back to sleep independently during the night</li>
      <li>Show you how to teach your child to take healthful, restorative naps</li>
      <li>Learn</li>
    </ul>
  </div>

  <svg class="abs" style="left:0;top:520px" width="540" height="110" viewBox="0 0 540 110">
    <path d="M0 54 C90 20 180 20 270 40 C360 60 450 34 540 46 L540 70 C450 58 360 84 270 64 C180 44 90 46 0 76Z" fill="var(--rose-soft)"/>
    <path d="M0 76 C90 46 180 44 270 64 C360 84 450 58 540 70 L540 110 L0 110Z" fill="#fff"/>
  </svg>

  <div class="abs photo-round" style="left:78px;top:499px;width:124px;height:124px" role="img" aria-label="Photograph of a baby's small hand resting in an adult hand"></div>
  <div class="abs photo-round" style="left:194px;top:456px;width:150px;height:150px" role="img" aria-label="Photograph of two young siblings asleep side by side"></div>
  <div class="abs photo-round" style="left:345px;top:501px;width:120px;height:120px" role="img" aria-label="Photograph of a toddler sleeping on a white pillow"></div>

  <div class="abs contact-h" style="left:0;width:540px;text-align:center;top:626px;font-size:20px">Contact Us:</div>
  <div class="abs contact-name" style="left:0;width:540px;text-align:center;top:652px;font-size:14.5px">Marta Lindqvist</div>

  <ul class="abs contact-list" style="left:48px;top:680px;font-size:11.5px">
    <li style="height:16px"><svg class="ico" viewBox="0 0 10 10"><path d="M2 1 L4 1 L4.6 3.3 L3.4 4.2 C4 5.6 4.6 6.2 5.8 6.8 L6.8 5.6 L9 6.2 L9 8.2 C6 9.5 0.6 4 2 1Z" fill="var(--rose)"/></svg>+34 612 384 705</li>
    <li style="height:16px"><svg class="ico" viewBox="0 0 10 10"><path d="M5 9.5 C2 6 1.8 4.6 1.8 3.8 A3.2 3.2 0 0 1 8.2 3.8 C8.2 4.6 8 6 5 9.5Z" fill="var(--rose)"/><circle cx="5" cy="3.8" r="1.2" fill="#fff"/></svg>Carrer de la Prada 14</li>
    <li style="height:14px;padding-left:18px">08000 Barcelona</li>
  </ul>
  <div class="abs divider" style="left:254px;top:680px;height:40px"></div>
  <ul class="abs contact-list" style="left:288px;top:680px;font-size:11.5px">
    <li style="height:16px"><svg class="ico" viewBox="0 0 10 10"><rect x="1" y="2" width="8" height="6" fill="none" stroke="var(--rose)" stroke-width="1.3"/><path d="M1 2 L5 5.5 L9 2" fill="none" stroke="var(--rose)" stroke-width="1.1"/></svg>info@quietmeadownest-example.com</li>
    <li style="height:16px"><svg class="ico" viewBox="0 0 10 10"><circle cx="5" cy="5" r="3.8" fill="none" stroke="var(--rose)" stroke-width="1.3"/><path d="M1.2 5 H8.8" stroke="var(--rose)" stroke-width="1"/></svg>www.quietmeadownest-example.com</li>
  </ul>
</section>

</body>
</html>
```